Construction company business card

One side to be the logo with the company name, The other side I would like: (Tomas verbick) Project manager 41 barrow crescent hallam 52917306224783(03) 9703 2428Info@gudeljgroup.comAnd then maybe a couple dot points saying what we do:Construction (commercial & industrial) Civil construction

Anything else please contact me!
Maybe curved st one edge of the card

Target Market(s)

Older clientele

Industry/Entity Type

Construction Company

Contact Information for Business Card

Read above

Colors
3277b5
1b1b1b
9d9d9d

Requirements
Must have
• Use my logo on one side
Nice to have
• Read above
Should not have
• Read above

```html
<!DOCTYPE html>
<html lang="en">
<head>
<meta charset="utf-8">
<title>Sternway Property Group – Business Card</title>
<link href="https://fonts.googleapis.com/css2?family=Lato:wght@400;700;900&display=swap" rel="stylesheet">
<style>
  :root {
    --brand-blue: #3277b5;
    --ink: #1b1b1b;
    --mid-grey: #9d9d9d;
    --text-grey: #444444;
    --card-white: #ffffff;
    --backdrop: #e4e4e4;
  }
  * { margin: 0; padding: 0; box-sizing: border-box; }
  html, body {
    width: 1200px;
    height: 802px;
    overflow: hidden;
  }
  body {
    background: var(--backdrop);
    font-family: "Lato", Arial, sans-serif;
    position: relative;
  }
  .card {
    position: absolute;
    top: 274px;
    width: 442px;
    height: 265px;
    box-shadow: 2px 3px 6px rgba(0, 0, 0, 0.35);
  }
  .card--front { left: 136px; background: var(--card-white); }
  .card--back  { left: 624px; background: var(--brand-blue); }

  .brand-mark {
    position: absolute;
    left: 288px;
    top: 28px;
    width: 76px;
    height: 76px;
    border-radius: 50%;
    background: var(--brand-blue);
  }
  .brand-name {
    position: absolute;
    right: 31px;
    top: 110px;
    text-align: right;
    color: var(--brand-blue);
    font-weight: 900;
    line-height: 1;
  }
  .brand-name__main { display: block; font-size: 28px; letter-spacing: 1px; }
  .brand-name__sub  { display: block; font-size: 9px; letter-spacing: 5.4px; margin-top: 2px; margin-right: -5px; }

  .person {
    position: absolute;
    left: 28px;
    top: 139px;
  }
  .person__name {
    font-size: 17px;
    font-weight: 400;
    color: var(--brand-blue);
    text-transform: uppercase;
    line-height: 1;
  }
  .person__role {
    font-size: 12px;
    color: var(--text-grey);
    margin-top: 2px;
    line-height: 1;
  }
  .divider {
    position: absolute;
    left: 120px;
    top: 164px;
    width: 291px;
    height: 1px;
    background: var(--mid-grey);
  }
  .contact {
    position: absolute;
    left: 28px;
    top: 178px;
    list-style: none;
    font-size: 12px;
    color: var(--text-grey);
    line-height: 16px;
  }
  .contact li { display: flex; align-items: center; gap: 3px; }
  .contact svg { width: 10px; height: 10px; fill: var(--brand-blue); }
  .contact__address { margin-top: 6px; padding-left: 2px; }

  .services {
    position: absolute;
    right: 31px;
    top: 200px;
    list-style: none;
    font-size: 12px;
    color: var(--text-grey);
    line-height: 15.5px;
    text-align: right;
  }
  .services__dot {
    display: inline-block;
    width: 8px;
    height: 8px;
    border-radius: 50%;
    background: var(--brand-blue);
    margin-left: 4px;
    vertical-align: middle;
  }
  .services__note { padding-right: 12px; }

  .back-name {
    position: absolute;
    left: 0;
    right: 0;
    top: 104px;
    text-align: center;
    color: var(--card-white);
    font-weight: 900;
    line-height: 1;
  }
  .back-name__main { display: block; font-size: 44px; letter-spacing: 2px; }
  .back-name__sub  { display: block; font-size: 13px; letter-spacing: 8.5px; margin-top: 4px; margin-right: -8.5px; }
</style>
</head>
<body>

  <section class="card card--front" aria-label="Business card front">
    <div class="brand-mark" aria-hidden="true"></div>
    <div class="brand-name">
      <span class="brand-name__main">STERNWAY</span>
      <span class="brand-name__sub">PROPERTY GROUP</span>
    </div>

    <div class="person">
      <p class="person__name">Tomas Verbick</p>
      <p class="person__role">Project manager</p>
    </div>
    <div class="divider"></div>

    <ul class="contact">
      <li>
        <svg viewBox="0 0 10 10" aria-hidden="true"><path d="M1 3.5C1 2 3 1.5 5 1.5S9 2 9 3.5L7.5 4 7 3H3L2.5 4ZM2.5 5h5l1 3.5h-7Z"/></svg>
        7306224783
      </li>
      <li>
        <svg viewBox="0 0 10 10" aria-hidden="true"><path d="M3 0.5h4v9H3ZM3.8 1.5v6h2.4v-6Z"/></svg>
        (03) 9418 6573
      </li>
      <li>
        <svg viewBox="0 0 10 10" aria-hidden="true"><path d="M0.5 2h9v6h-9ZM1.2 2.6 5 5.6 8.8 2.6Z"/></svg>
        Info@verbickgroup.com
      </li>
      <li class="contact__address">41 barrow crescent kelmara 5291</li>
    </ul>

    <ul class="services">
      <li>Construction<span class="services__dot"></span></li>
      <li class="services__note">(commercial &amp; industrial)</li>
      <li>Civil construction<span class="services__dot"></span></li>
    </ul>
  </section>

  <section class="card card--back" aria-label="Business card back">
    <div class="back-name">
      <span class="back-name__main">STERNWAY</span>
      <span class="back-name__sub">PROPERTY GROUP</span>
    </div>
  </section>

</body>
</html>
```